BildeVOLD buisnesscard

Hey :) I need a modern buisnesscard for my company BildeVOLD
It most have:
Dagligleder og Fotograf: Henrik Audun Strandvik

Mob: +4791264085
Epost: post@bildevold.example
Adresse: Kvernbakken9, 6040 Langevåg

Facbook and instagram logo with text BildeVOLD

BildeVOLD logo

It Company

```html
<!DOCTYPE html>
<html lang="no">
<head>
<meta charset="utf-8">
<title>BildeVOLD – visittkort</title>
<link rel="stylesheet" href="https://fonts.googleapis.com/css2?family=Exo+2:wght@600;700&family=Roboto:wght@400;500&display=swap">
<style>
  :root {
    --page: #d9d7d4;
    --card-black: #131313;
    --card-charcoal: #1c1c1c;
    --band-grey: #a9abad;
    --stripe-dark: #262626;
    --text-light: #c9cacb;
    --text-muted: #8e9092;
    --text-white: #f2f2f2;
    --text-dark: #2a2a2a;
  }
  * { box-sizing: border-box; margin: 0; padding: 0; }
  html, body { width: 1200px; height: 716px; overflow: hidden; }
  body {
    background: var(--page);
    font-family: "Roboto", Arial, sans-serif;
    position: relative;
  }
  .card {
    position: absolute;
    top: 208px;
    width: 540px;
    height: 300px;
    border-radius: 4px;
    overflow: hidden;
    box-shadow: 0 10px 28px rgba(0,0,0,.28);
  }
  .card--back {
    left: 40px;
    background: var(--card-black);
    display: flex;
    align-items: center;
    justify-content: center;
  }
  .back-wordmark {
    font-family: "Exo 2", Arial, sans-serif;
    font-weight: 700;
    font-size: 44px;
    color: #2c2c2c;
    letter-spacing: .5px;
  }
  .card--front {
    left: 620px;
    background: var(--card-charcoal);
  }
  .front-waves {
    position: absolute;
    inset: 0;
    width: 540px;
    height: 300px;
  }
  .brand {
    position: absolute;
    left: 34px;
    top: 108px;
    font-family: "Exo 2", Arial, sans-serif;
    font-weight: 700;
    font-size: 40px;
    color: var(--band-grey);
  }
  .social {
    position: absolute;
    left: 36px;
    top: 170px;
    display: flex;
    align-items: center;
    gap: 7px;
    font-size: 13px;
    color: var(--text-muted);
  }
  .social-mark {
    width: 12px;
    height: 12px;
    background: var(--text-muted);
    border-radius: 2px;
  }
  .holder {
    position: absolute;
    right: 20px;
    top: 58px;
    text-align: right;
  }
  .holder-name {
    font-family: "Exo 2", Arial, sans-serif;
    font-weight: 700;
    font-size: 18px;
    color: var(--text-white);
  }
  .holder-role {
    margin-top: 3px;
    font-size: 12.5px;
    line-height: 1.25;
    color: var(--text-dark);
  }
  .contact {
    position: absolute;
    right: 20px;
    bottom: 24px;
    list-style: none;
    text-align: right;
    font-size: 13px;
    color: var(--text-light);
  }
  .contact li {
    display: flex;
    justify-content: flex-end;
    align-items: center;
    gap: 8px;
    line-height: 21px;
  }
  .contact svg { width: 11px; height: 11px; fill: var(--text-light); }
</style>
</head>
<body>

<section class="card card--back" aria-label="Kortets bakside">
  <span class="back-wordmark">BildeVOLD</span>
</section>

<section class="card card--front" aria-label="Kortets forside">
  <svg class="front-waves" viewBox="0 0 540 300" aria-hidden="true">
    <path d="M120 0 H540 V205 C470 150 380 110 300 70 C230 35 170 15 120 0 Z" fill="var(--band-grey)"/>
    <path d="M150 0 C260 30 370 80 540 175" stroke="var(--stripe-dark)" stroke-width="7" fill="none"/>
    <path d="M175 20 C290 55 400 110 540 200" stroke="var(--stripe-dark)" stroke-width="4" fill="none"/>
    <path d="M300 120 C400 150 470 185 540 215" stroke="var(--band-grey)" stroke-width="3" fill="none"/>
  </svg>

  <div class="brand">BildeVOLD</div>
  <div class="social"><span class="social-mark"></span>/BildeVOLD</div>

  <div class="holder">
    <div class="holder-name">Henrik Audun Strandvik</div>
    <div class="holder-role">Managing Director<br>&amp; Photographer</div>
  </div>

  <ul class="contact">
    <li>+4791264085
      <svg viewBox="0 0 12 12"><path d="M3 0h6a1 1 0 0 1 1 1v10a1 1 0 0 1-1 1H3a1 1 0 0 1-1-1V1a1 1 0 0 1 1-1zm0 1.5v8h6v-8z"/></svg>
    </li>
    <li>post@bildevold.example
      <svg viewBox="0 0 12 12"><path d="M0 2h12v8H0zm1 1.2V9h10V3.2L6 6.5z"/></svg>
    </li>
    <li>www.bildevold.example
      <svg viewBox="0 0 12 12"><path d="M6 0a6 6 0 1 0 0 12A6 6 0 0 0 6 0zm0 1c.7.8 1.2 2.4 1.3 4.5H4.7C4.8 3.4 5.3 1.8 6 1zM1 6.5h2.7c.1 1.7.5 3.1 1 4A5 5 0 0 1 1 6.5zm0-1a5 5 0 0 1 3.7-4c-.5.9-.9 2.3-1 4zm5 5.5c-.7-.8-1.2-2.4-1.3-4.5h2.6C7.2 8.6 6.7 10.2 6 11zm1.3-.5c.5-.9.9-2.3 1-4H11a5 5 0 0 1-3.7 4zm1-5c-.1-1.7-.5-3.1-1-4A5 5 0 0 1 11 5.5z"/></svg>
    </li>
    <li>Kvernbakken9, 6040 Langevåg
      <svg viewBox="0 0 12 12"><path d="M6 0a4 4 0 0 0-4 4c0 3 4 8 4 8s4-5 4-8a4 4 0 0 0-4-4zm0 5.5A1.5 1.5 0 1 1 6 2.5a1.5 1.5 0 0 1 0 3z"/></svg>
    </li>
  </ul>
</section>

</body>
</html>
```